Buch-/E-Book-Cover
Tolle Designerin. Tolles Ergebnis. Das beste war die reibungslose Kommunikation.
Zielgruppe
Wir verkaufen Trainings und vermitteln über unser Buch ein erstes vertieftes Wissen zum Thema Vermögensaufbau.
Aufgabenstellung
Es soll schlicht und schön sein, Angelehnt an Smart mom slow mom, bzw. an Plane klug und bleibe frei von Gideon Farrow.
Wir benötigen die AI, etc Dateien und die fertigen Dateien für Bucholo.de Lesquill sowie Bucholo.de Books (ehemals Printvelle) mit fertigem Cover.
Vorgaben von Bucholo.de über die Homepage. Anbei ein Beispiel (wegen Bucholo.de Buchnummer etc) Abstände, Buchrücken etc.
Buch ca. 150 Seiten
https://www.bucholo-beispiel.de/Gaertner-sein-trotzdem-Freude-kleinen/dp/7302958163 Front und Backcover kann man sich da ansehen.
Der Buchtitel ist 'Baue Mauern und bleibe still' - - Lassen Sie uns freundschaftlich in entspannter Atmosphäre über Immobilien sprechen (der nebentitel so klein wie bei Smart Mom - Slow Mom)
Rücktitel: Bitte zuerst Platzhalter.
Ich bitte um 5x8 inch, also wie DIN A 5, wir nehmen cremefarbenes Papier denke ich. Die Seitenzahl kann ich auf die Seite noch nicht sagen, wir haben aber 75 Din A4 Seiten, sprich nach Formatierung eher 160-165 Din A5. WErde ich Ihnen final nach dem Gewinn sagen.
Versuchen Sie mich mal aus dem einen Bild raus zu schneiden, und dass dann mit einem Layer über das cover zu legen.
2-3 Versionen wäre gut, mit 2-3 Bildern. Buchrücken ein kleines Bild von mir.
Seite vom Buch: Titel nochmal.

```html
<!DOCTYPE html>
<html lang="de">
<head>
<meta charset="utf-8">
<title>Buchcover – Lennart Lorenz</title>
<link href="https://fonts.googleapis.com/css2?family=Fira+Sans:wght@600;700&family=Montserrat:wght@700;800;900&family=Open+Sans:wght@600;700&display=swap" rel="stylesheet">
<style>
  :root {
    --blue-deep: #040c2a;
    --blue-mid: #1a3f8c;
    --gold: #f9d423;
    --white: #ffffff;
    --silver: #e4e7ee;
    --photo-dark: #3a3640;
    --photo-light: #8a7f86;
    --barcode-field: #ffffff;
  }
  * { margin: 0; padding: 0; box-sizing: border-box; }
  html, body { width: 1200px; height: 927px; overflow: hidden; background: var(--blue-deep); }
  .cover {
    position: relative; width: 1200px; height: 927px; overflow: hidden;
    background:
      radial-gradient(ellipse 560px 420px at 930px 40px, rgba(140,180,235,.85), transparent 70%),
      radial-gradient(ellipse 700px 700px at 820px 300px, var(--blue-mid), transparent 80%),
      linear-gradient(100deg, var(--blue-deep) 0%, #0d2463 35%, #1e4a9c 65%, #123579 100%);
  }
  .back-headline {
    position: absolute; left: 0; width: 590px; top: 48px; text-align: center;
    font: 700 23px/1 "Fira Sans", sans-serif; color: var(--gold);
  }
  .back-copy {
    position: absolute; left: 42px; top: 96px; width: 504px;
    font: 600 17px/21.9px "Fira Sans", sans-serif; color: var(--white);
    text-align: justify;
  }
  .back-copy p + p { margin-top: 21.9px; }
  .back-portrait {
    position: absolute; left: 45px; top: 565px; width: 250px; height: 350px;
    border-radius: 90px 90px 10px 10px;
    background: linear-gradient(180deg, var(--photo-light), var(--photo-dark));
    opacity: .8;
  }
  .barcode-field { position: absolute; left: 325px; top: 753px; width: 223px; height: 131px; background: var(--barcode-field); }
  .spine-text {
    position: absolute; left: 610px; transform-origin: 0 0; transform: rotate(90deg);
    font-family: "Montserrat", sans-serif; font-weight: 900; line-height: 1; white-space: nowrap;
  }
  .spine-author { top: 45px; font-size: 24px; color: var(--white); }
  .spine-title { top: 434px; font-size: 21px; color: var(--gold); }
  .front-portrait {
    position: absolute; left: 630px; top: 282px; width: 535px; height: 645px;
    border-radius: 240px 240px 0 0;
    background: radial-gradient(ellipse at 50% 25%, var(--photo-light), var(--photo-dark) 70%);
    opacity: .75;
  }
  .front-title { position: absolute; left: 0; top: 0; }
  .title-word { font-family: "Montserrat", sans-serif; font-weight: 900; fill: var(--gold); }
  .author-line { font-family: "Montserrat", sans-serif; font-weight: 800; fill: var(--white); }
  .series-line { font-family: "Open Sans", sans-serif; font-weight: 700; fill: var(--silver); }
  .tagline {
    position: absolute; left: 872px; top: 526px; width: 300px; text-align: center;
    font: 600 17.5px/23.5px "Open Sans", sans-serif; color: var(--white);
    text-shadow: 0 1px 3px rgba(0,0,0,.6);
  }
</style>
</head>
<body>
<div class="cover">
  <h2 class="back-headline">BAUE MAUERN UND BLEIBE STILL!</h2>
  <div class="back-copy">
    <p>Das klingt für Sie nach Widerspruch? Dann kennen Sie WohnwertCoach Lennart Lorenz (Ex-Lehrer) noch nicht: Schritt für Schritt berichtet er von seinem erstaunlichen Werdegang und seinem Erfolg als Immobilieninvestor. Erfahren Sie von ihm aus erster Hand, wie Sie an Ihr Start-Objekt gelangen und auf dem Immobilienmarkt bestehen. Als ehemalige Lehrkraft bringt Lennart Lorenz die Dinge allgemein verständlich und gebündelt auf den Punkt. Profitieren Sie von seiner breiten Erfahrung, lernen Sie aus den im Ratgeber aufgeführten, persönlichen Gesprächen, alles, was Sie wissen müssen – und werden Sie selbst zum WohnwertCoach.</p>
    <p>Ein Denkanstoß gefällig? Bei derzeit 1 % Zinsen und gleichzeitiger Inflation von 3 % können Sie praktisch dabei zusehen, wie Ihre Schulden mit jedem Tag schrumpfen.</p>
    <p>Praxisrelevant, authentisch und auf Augenhöhe mit seinen Lesern – der WohnwertCoach bietet Ihnen in „Baue Mauern und bleibe still!“ alles, um noch heute mit einem neuen, unabhängigen Leben zu beginnen. Fangen Sie gleich damit an!</p>
  </div>
  <div class="back-portrait" role="img" aria-label="Foto des Autors auf der Bühne, einen Geldschein hochhaltend"></div>
  <div class="barcode-field"></div>

  <div class="spine-text spine-author">LENNART LORENZ</div>
  <div class="spine-text spine-title">BAUE MAUERN UND BLEIBE STILL</div>

  <div class="front-portrait" role="img" aria-label="Foto des Autors im Sakko, sprechend mit ausgebreiteten Händen"></div>

  <svg class="front-title" width="1200" height="927" viewBox="0 0 1200 927">
    <text class="author-line" x="650" y="60" font-size="21" textLength="507" lengthAdjust="spacingAndGlyphs">LENNART LORENZ - DER WOHNWERTCOACH</text>
    <text class="title-word" x="650" y="190" font-size="152" textLength="502" lengthAdjust="spacingAndGlyphs">BAUE</text>
    <text class="title-word" x="650" y="282" font-size="100" textLength="507" lengthAdjust="spacingAndGlyphs">MAUERN</text>
    <text class="series-line" x="648" y="352" font-size="19" textLength="188" lengthAdjust="spacingAndGlyphs">GESPRÄCHE ÜBER</text>
    <text class="series-line" x="647" y="396" font-size="28" textLength="190" lengthAdjust="spacingAndGlyphs">IMMOBILIEN</text>
    <text class="title-word" x="648" y="745" font-size="52" textLength="90" lengthAdjust="spacingAndGlyphs">und</text>
    <text class="title-word" x="758" y="745" font-size="86" textLength="352" lengthAdjust="spacingAndGlyphs">BLEIBE</text>
    <text class="title-word" x="650" y="885" font-size="170" textLength="505" lengthAdjust="spacingAndGlyphs">STILL</text>
  </svg>

  <p class="tagline">Lassen Sie uns freundschaftlich<br>in entspannter Atmosphäre<br>über Immobilien sprechen</p>
</div>
</body>
</html>
```